Wordpress website design for a high-end painting business

We are currently rebranding and are looking to update our Wordpress theme. We have recently rebranded our logo on PixelHarbor, and would like our website to be equally as refined.
Our business is named “Fenwick Painters”. We are a high-end painting business that is known for being professional and having high standards. Our clean and professional image is important as it separates us from our competition. Our current website can be found at www.fenwickcoatings.co.nz . We designed the site ourselves so it is understandably rudimentary. We are generally happy with the. page layout of our existing site, but we like a professional remodel. Any ideas on improvement welcomed.
We would like the front page of the website to summarise all of the info throughout the whole website (I.e introduction, photos, testimonials, contact info etc.) as visitors typically scroll through the first page to see that we are reputable and get to our contact number/email contact at the bottom of the page. We would like this first page to give a clean well rounded image of our business. We would like the gallery to be a scroll through of large photos, as it is difficult to see paint details in smaller photos. A contact page with an enquiry section would also be good.
For the colour scheme, we would like something that fits a bold, masculine and high end theme (similar to our logo attached).
We would like the footer to include Velmora paint logos and the plain badge shape logo we have included as these are important to our profession.
We have attached some photos of our work also. I will add more in the coming days. More can also be found on our website.
If you have questions or comments, please don’t hesitate to ask and I will get back as soon as possible.
We are open to your own interpretation or ideas for a better layout/site provided they fit the general brief of being a well rounded site for our profession.
Thanks,
Fenwick Painters.
Target Market(s)
High end clients
Industry/Entity Type
Painting (interior and exterior)
Coding
Coded - Design and coding required
Requirements
Must have
- Classy feel, separating us from typical painting companies. Well rounded homepage.
Nice to have
- Lots of examples of our work
Should not have
- Untidy paint motifs (eg, paint droplets, paint splashes)

```html
<!DOCTYPE html>
<html lang="en">
<head>
<meta charset="utf-8">
<title>Fenwick Painters</title>
<link href="https://fonts.googleapis.com/css2?family=Roboto+Slab:wght@300;400;500;700&family=Open+Sans:wght@400;600;700&display=swap" rel="stylesheet">
<style>
:root{
  --ink:#1f2430;
  --navy:#1a2130;
  --brown:#6e4a26;
  --brown-soft:#9a6e3f;
  --cream:#f6dfba;
  --gray:#ececec;
  --light:#f4f3f4;
  --blue:#1d4b74;
  --blue-dark:#123454;
  --white:#ffffff;
  --text:#333333;
  --muted:#9aa0ab;
}
*{box-sizing:border-box;margin:0;padding:0}
html,body{width:1200px;height:4468px;overflow:hidden}
body{font-family:"Roboto Slab",serif;color:var(--text);background:var(--white);position:relative}
.abs{position:absolute}
.btn{position:absolute;border:2px solid currentColor;border-radius:30px;display:flex;align-items:center;justify-content:center;font-size:15px;font-family:"Roboto Slab",serif}

/* top bar */
.topbar{position:absolute;left:0;top:0;width:1200px;height:31px;background:var(--ink);color:#dfe2e8;font-size:14px}
.topbar .mail{left:160px;top:7px;display:flex;gap:10px;align-items:center}
.topbar .follow{right:160px;top:6px;display:flex;gap:14px;align-items:center}
.dot-icon{width:10px;height:10px;border-radius:50%;background:#dfe2e8;display:inline-block}

/* nav */
.nav{position:absolute;left:0;top:31px;width:1200px;height:69px;background:var(--white)}
.nav ul{position:absolute;left:328px;top:25px;display:flex;gap:24px;list-style:none;font-size:14px;color:#6b6b6b}
.nav li.active{color:var(--ink);font-weight:500}
.estimate{position:absolute;left:806px;top:31px;width:394px;height:69px;background:var(--ink);color:var(--white);clip-path:polygon(4% 0,100% 0,100% 100%,0 100%)}
.estimate .ring{position:absolute;left:46px;top:14px;width:40px;height:40px;border-radius:50%;background:var(--brown-soft)}
.estimate small{position:absolute;left:94px;top:16px;font-size:10px;font-family:"Open Sans",sans-serif}
.estimate strong{position:absolute;left:94px;top:31px;font-size:18px;font-weight:500;letter-spacing:1px}
.badge{position:absolute;left:165px;top:31px;width:156px;height:139px;background:var(--white);clip-path:polygon(0 0,100% 0,88% 100%,12% 100%);display:flex;flex-direction:column;align-items:center;justify-content:flex-end;padding-bottom:14px;z-index:3}
.badge .mark{width:60px;height:60px;border-radius:50%;background:var(--ink);margin-bottom:8px}
.badge span{font-size:15px;font-weight:700;color:var(--ink)}

/* hero */
.hero{position:absolute;left:0;top:100px;width:1200px;height:538px;background:linear-gradient(180deg,#3c4247,#4a5346 60%,#2f3a28)}
.hero .panel{position:absolute;right:0;top:0;width:720px;height:538px;background:var(--brown);clip-path:path("M720 0 L720 538 L0 538 C120 470 300 420 330 300 C360 180 430 60 460 0 Z")}
.hero h1{position:absolute;right:156px;top:128px;text-align:right;font-weight:400;color:var(--white);font-size:52px;line-height:66px}
.hero .btn{left:900px;top:346px;width:142px;height:50px;color:var(--white)}
.hero .dots{position:absolute;left:576px;top:488px;display:flex;gap:9px}
.hero .dots i{width:10px;height:10px;border-radius:50%;border:1.5px solid #ccc}
.hero .dots i:first-child{background:#ccc}

/* about */
.about{position:absolute;left:0;top:638px;width:1200px;height:595px;background:var(--white)}
.about .drip{position:absolute;right:0;top:0;width:82px;height:300px;background:var(--brown);border-radius:0 0 0 40px}
.about .big{position:absolute;left:512px;top:38px;width:520px;height:520px;border-radius:50%;background:var(--gray)}
.about .ring{position:absolute;left:157px;top:108px;width:380px;height:380px;border-radius:50%;border:7px solid var(--cream)}
.about .photo{position:absolute;left:197px;top:148px;width:300px;height:300px;border-radius:50%;background:linear-gradient(160deg,#d8dde0,#8f9a8c 60%,#9b3f3a)}
.about .mini{position:absolute;left:425px;top:230px;width:140px;height:140px;border-radius:50%;background:var(--white)}
.about .pin{position:absolute;width:12px;height:12px;border-radius:50%;background:var(--brown-soft)}
.about h2{position:absolute;left:635px;top:126px;font-size:48px;font-weight:400;color:var(--ink)}
.about .copy{position:absolute;left:635px;top:200px;width:360px;font-family:"Open Sans",sans-serif;font-size:13.5px;line-height:22.5px;color:#333}
.about .copy p{margin-bottom:22px}
.about .btn{left:635px;top:423px;width:142px;height:46px;color:var(--ink)}

/* services */
.services{position:absolute;left:0;top:1233px;width:1200px;height:633px;background:radial-gradient(circle at 50% 55%,#2a6392,var(--blue) 45%,var(--blue-dark))}
.services h2{position:absolute;left:0;width:1200px;top:50px;text-align:center;color:var(--white);font-weight:400;font-size:52px}
.pill{position:absolute;width:272px;height:113px;background:#e4e3e1;border-radius:60px;border:3px solid var(--cream);display:flex;align-items:center;font-size:19px;color:var(--ink);line-height:25px}
.pill .thumb{position:absolute;top:-3px;width:113px;height:113px;border-radius:50%;background:var(--white);border:3px solid #ddd}
.pill .thumb i{position:absolute;inset:8px;border-radius:50%}
.pill.l{left:160px;padding-left:135px}
.pill.l .thumb{left:-3px}
.pill.r{left:756px;padding-left:50px}
.pill.r .thumb{right:-3px}
.pill.hot{background:var(--brown-soft);color:var(--white);padding-left:36px;text-align:center}
.hub{position:absolute;left:465px;top:224px;width:270px;height:270px;border-radius:50%;background:var(--white);border:10px solid #e3e3e3;display:flex;align-items:center;justify-content:center;font-size:26px;font-weight:700;color:var(--ink)}

/* gallery */
.gallery{position:absolute;left:0;top:1866px;width:1200px;height:1039px;background:var(--white)}
.gallery h2{position:absolute;left:160px;top:70px;font-size:52px;font-weight:400;color:var(--ink)}
.shot{position:absolute;border:4px solid var(--white);box-shadow:0 4px 12px rgba(0,0,0,.18)}
.caption{position:absolute;left:0;right:0;bottom:0;height:72px;background:rgba(110,74,38,.85);color:var(--white);font-size:18px;display:flex;align-items:center;padding-left:18px}
.gallery .btn{left:529px;top:901px;width:142px;height:53px;color:var(--ink)}

/* testimonials */
.testimonials{position:absolute;left:0;top:2905px;width:1200px;height:608px;background:var(--navy)}
.testimonials h2{position:absolute;left:0;width:1200px;top:70px;text-align:center;color:var(--white);font-size:52px;font-weight:400}
.card{position:absolute;top:161px;width:274px;height:279px;background:#3b3f47;border-radius:0 0 46px 0;padding:48px 28px 0;color:#d6d8dc;font-family:"Open Sans",sans-serif}
.card.hot{background:linear-gradient(180deg,#a47b4b,#c09363)}
.card .q{font-family:"Roboto Slab",serif;font-size:30px;color:#7c6a55;line-height:20px;height:22px}
.card.hot .q{color:#ead7bd}
.card p{font-size:15px;line-height:22px;margin-top:8px;width:200px}
.card .who{font-weight:700;font-size:16px;letter-spacing:.5px;margin-top:26px;line-height:26px;color:#e7e8ea}
.card .go{position:absolute;right:28px;bottom:30px;width:36px;height:36px;border-radius:50%;background:var(--white)}
.testimonials .more{position:absolute;left:0;width:1200px;top:514px;text-align:center;color:var(--white);font-size:15px}

/* quote */
.quote{position:absolute;left:0;top:3513px;width:1200px;height:498px;background:#e9e8e9;overflow:hidden}
.quote .curve{position:absolute;left:-200px;top:-600px;width:1180px;height:1000px;border-radius:50%;background:var(--white)}
.quote h2{position:absolute;left:157px;top:45px;font-size:52px;font-weight:400;color:var(--ink)}
.field{position:absolute;background:var(--white);border:1.5px solid #c9c9c9;border-radius:4px;font-family:"Open Sans",sans-serif;font-size:13px;color:#444;padding:12px 10px}
.quote .btn{left:160px;top:397px;width:143px;height:52px;color:var(--ink);background:#eee}
.quote .art{position:absolute;left:745px;top:24px;width:455px;height:474px;background:radial-gradient(circle at 70% 40%,#8a8c90,#b99066 45%,rgba(233,232,233,0) 70%);opacity:.55}

/* footer */
.footer{position:absolute;left:0;top:4011px;width:1200px;height:457px;background:var(--navy);color:#c9ccd2;font-family:"Open Sans",sans-serif;font-size:14px}
.footer h4{position:absolute;font-family:"Roboto Slab",serif;font-weight:400;font-size:20px;color:var(--brown-soft)}
.footer .brand{position:absolute;left:160px;top:116px;width:120px;display:flex;flex-direction:column;align-items:center;gap:10px}
.footer .brand .mark{width:104px;height:104px;border-radius:50%;background:#e8e4de}
.footer .brand b{font-family:"Roboto Slab",serif;font-size:16px;color:var(--white);white-space:nowrap}
.footer .social{position:absolute;left:160px;top:307px;display:flex;gap:11px}
.footer .social i{width:26px;height:26px;border-radius:50%;background:var(--brown-soft)}
.footer ul{position:absolute;left:349px;top:152px;list-style:none;line-height:31px}
.loc{position:absolute;left:524px;display:flex;gap:16px;align-items:flex-start;line-height:20px}
.loc i{width:26px;height:26px;border-radius:50%;background:#e7d9c6;flex:none}
.footer .nl{position:absolute;left:789px;top:148px;width:260px;line-height:22px}
.footer .mailbox{position:absolute;left:789px;top:203px;width:253px;height:44px;background:var(--white);border-radius:4px;color:#333;font-size:14px;padding:12px 32px}
.footer .sub{position:absolute;left:789px;top:258px;width:144px;height:50px;border:2px solid var(--white);border-radius:26px;color:var(--white);display:flex;align-items:center;justify-content:center;font-size:15px}
.footer .copy{position:absolute;left:160px;top:386px;font-size:11px}
.footer .copy em{font-style:normal;color:var(--brown-soft)}
.partner{position:absolute;top:372px;height:38px;border-radius:3px}
</style>
</head>
<body>

<div class="topbar">
  <div class="abs mail"><span class="dot-icon" style="border-radius:2px;width:14px"></span>hello@fenwickpainters.co.nz</div>
  <div class="abs follow">Follow Us :<span class="dot-icon"></span><span class="dot-icon"></span><span class="dot-icon"></span></div>
</div>

<header class="nav">
  <ul>
    <li class="active">Home</li><li>About</li><li>Services</li><li>Gallery</li><li>All Testimonials</li><li>Contact</li>
  </ul>
</header>
<div class="estimate">
  <div class="ring"></div>
  <small>Schedule A Painting Estimate</small>
  <strong>021 - 555 - 0148</strong>
</div>
<div class="badge"><div class="mark"></div><span>Fenwick Painters</span></div>

<section class="hero">
  <div class="abs" role="img" aria-label="Photo of a freshly painted weatherboard house" style="left:0;top:0;width:620px;height:538px;background:linear-gradient(180deg,#4a5058,#6f7a80 45%,#3d4a2e)"></div>
  <div class="panel"></div>
  <h1>The Highest<br>Quality<br>Paint-Work</h1>
  <div class="btn">Get In Touch</div>
  <div class="dots"><i></i><i></i><i></i></div>
</section>

<section class="about">
  <div class="drip"></div>
  <div class="big"></div>
  <div class="ring"></div>
  <div class="photo" role="img" aria-label="Photo of a worker waterblasting a roof"></div>
  <div class="mini"></div>
  <div class="pin" style="left:463px;top:155px"></div>
  <div class="pin" style="left:491px;top:403px"></div>
  <h2>About Us</h2>
  <div class="copy">
    <p>Here at Fenwick Painters, we take a lot of pride in our work. We strive to ensure the highest quality paint-work, paying close attention to detail to provide a long lasting finish.</p>
    <p>Here at Fenwick Painters, we take a lot of pride in our work. We strive to ensure the highest quality paint-work, paying close attention to detail to provide a long lasting finish.</p>
  </div>
  <div class="btn">Read More</div>
</section>

<section class="services">
  <h2>Our Services</h2>
  <div class="pill l" style="top:156px"><span class="thumb"><i role="img" aria-label="Photo of a painted house exterior" style="background:linear-gradient(#bcd2e6,#7e9a5a)"></i></span>Exterior<br>Painting</div>
  <div class="pill l" style="top:293px"><span class="thumb"><i role="img" aria-label="Photo of a painted interior room" style="background:linear-gradient(#e7e2da,#8c6a50)"></i></span>Interior<br>Painting</div>
  <div class="pill l" style="top:428px"><span class="thumb"><i role="img" aria-label="Photo of a papered wall" style="background:linear-gradient(#a7a399,#6b6960)"></i></span>Wall<br>papering</div>
  <div class="pill r" style="top:156px">Plastering<span class="thumb"><i role="img" aria-label="Photo of plaster being applied" style="background:linear-gradient(#cfcac2,#8a7666)"></i></span></div>
  <div class="pill r hot" style="top:293px">Waterblasting &amp; House<br>Cleaning</div>
  <div class="pill r" style="top:428px;padding-left:96px">Roof<br>Painting<span class="thumb"><i role="img" aria-label="Photo of a painted roof" style="background:linear-gradient(#dfe3e8,#5b6068)"></i></span></div>
  <div class="hub">Fenwick Painters</div>
</section>

<section class="gallery">
  <h2>Gallery</h2>
  <div class="shot" role="img" aria-label="Photo of a freshly painted empty room" style="left:160px;top:170px;width:440px;height:237px;background:linear-gradient(90deg,#d9d8d4,#f2f2f0 60%,#8b9a8a)"></div>
  <div class="shot" role="img" aria-label="Photo of a painted living room with fireplace" style="left:720px;top:128px;width:320px;height:238px;background:linear-gradient(160deg,#ecebe7,#b9bdbf 60%,#6e7a86)"></div>
  <div class="shot" role="img" aria-label="Photo of painted exterior weatherboards" style="left:160px;top:452px;width:272px;height:401px;background:linear-gradient(180deg,#e9ebea,#f4f4f2 55%,#9a5a3a 80%,#7a6d4a)"></div>
  <div class="shot" role="img" aria-label="Photo of a painted kitchen" style="left:714px;top:582px;width:321px;height:240px;background:linear-gradient(160deg,#ececea,#c7c9c6 50%,#6c4b38)"></div>
  <div class="shot" style="left:381px;top:246px;width:571px;height:428px;background:linear-gradient(180deg,#dfe3e6,#9aa7b3 45%,#5e7a45)" role="img" aria-label="Photo of an exterior repaint of a weatherboard house">
    <div class="caption">Exterior repaint in Harbourview, Northbridge.</div>
  </div>
  <div class="btn">View All</div>
</section>

<section class="testimonials">
  <h2>Testimonial</h2>
  <div class="card" style="left:160px"><div class="q">“</div><p>Sam and his Team have done an amazing job painting our house. ”</p><div class="who">MARTA KOWALEWSKA<br>(2019)</div><div class="go"></div></div>
  <div class="card hot" style="left:463px"><div class="q">“</div><p>Very happy with Fenwick decorators. Sam and Rowan did a great job. ”</p><div class="who">DOUGLAS REID<br>(2020)</div><div class="go"></div></div>
  <div class="card" style="left:766px"><div class="q">“</div><p>Sam and Rowan was prompt and efficient. Very friendly . ”</p><div class="who">NATHAN HO<br>(2020)</div><div class="go"></div></div>
  <div class="more">View All</div>
</section>

<section class="quote">
  <div class="curve"></div>
  <div class="art" role="img" aria-label="Large decorative archer illustration"></div>
  <h2>Request A Online Quote</h2>
  <div class="field" style="left:158px;top:123px;width:288px;height:42px">Name :</div>
  <div class="field" style="left:454px;top:123px;width:288px;height:42px">Phone</div>
  <div class="field" style="left:158px;top:174px;width:288px;height:42px">Email :</div>
  <div class="field" style="left:454px;top:174px;width:288px;height:42px">Address :</div>
  <div class="field" style="left:158px;top:226px;width:584px;height:42px">Service :<span style="position:absolute;right:12px">▾</span></div>
  <div class="field" style="left:158px;top:278px;width:584px;height:105px">Message :</div>
  <div class="btn">Send Message</div>
</section>

<footer class="footer">
  <div class="brand"><div class="mark"></div><b>Fenwick Painters</b></div>
  <div class="social"><i></i><i></i><i></i></div>
  <h4 style="left:349px;top:108px">Quick Link</h4>
  <ul><li>Home</li><li>About</li><li>Services</li><li>Gallery</li><li>All Testimonials</li><li>Contact</li></ul>
  <h4 style="left:524px;top:108px">Location</h4>
  <div class="loc" style="top:156px"><i></i><span>Rowan Kettering<br>Ashvale, Northbridge.</span></div>
  <div class="loc" style="top:220px"><i></i><span style="padding-top:3px">021 555 0148</span></div>
  <div class="loc" style="top:270px"><i></i><span style="padding-top:3px">hello@fenwickpainters.co.nz</span></div>
  <h4 style="left:789px;top:108px">Newsletter Sign Up</h4>
  <div class="nl">Get weekly access to our best deals</div>
  <div class="mailbox">Enter Mail Id</div>
  <div class="sub">Subscribe Now</div>
  <div class="copy">Copyright © 2022 <em>Fenwickpainters.</em> All Right Reserved</div>
  <div class="partner" style="left:659px;width:110px;background:#27367a"></div>
  <div class="partner" style="left:773px;width:222px;background:#1597d6"></div>
  <div class="partner" style="left:1000px;width:40px;border:2px solid #1597d6"></div>
</footer>

</body>
</html>
```